Brochure design for BRIXACURE clinic

We are seeking for a brochure design for new medical walk-in clinic.
The desirable design for the brochure will contain strong concept of positioning for
" convenience" of medical care in terms of access, affordability and service.
I am looking forward to having eye-catching modern design.
Updates

 I've updated the logo file to ai file

and for your reference please see our web page www.brixa-cure.com
to keep consistency in terms of  color scheme  and impression

Thanks

Dear Designers,

We'd like to make the deadline earlier by Dec 17(Tuesday) 
Thank you..

Target Market(s)

Age from 20 - 50

Industry/Entity Type

Medical

Colors
f78f20
33a6d7

Requirements
Must have
• Multi-language greeting line in Korean, Chinese, Japanese and English on the cover page.

8 x11.7 sized tri-fold
Nice to have
• Please refer to our web page in order to keep consistency
www.brixa-cure.com

```html
<!DOCTYPE html>
<html lang="en">
<head>
<meta charset="utf-8">
<title>BRIXACURE Tri-fold Brochure</title>
<link href="https://fonts.googleapis.com/css2?family=Questrial&family=Noto+Sans+KR&family=Noto+Sans+SC&family=Noto+Sans+JP&display=swap" rel="stylesheet">
<style>
  :root{
    --blue:#33a6d7;
    --orange:#f78f20;
    --red:#b8262c;
    --slate:#8c9ca8;
    --ink:#3d3d3d;
    --muted:#777;
    --paper:#ffffff;
    --stage:#e6e7e8;
    --rule:#c9d2d8;
    --frame:#eef0f2;
  }
  *{box-sizing:border-box;margin:0;padding:0}
  html,body{width:1200px;height:900px;overflow:hidden}
  body{background:var(--stage);font-family:"Questrial","Noto Sans KR","Noto Sans SC","Noto Sans JP",sans-serif;color:var(--ink);position:relative}
  .spread{position:absolute;left:296px;width:608px;height:430px;background:var(--paper);box-shadow:0 2px 8px rgba(0,0,0,.12);overflow:hidden}
  .spread--outside{top:12px;display:grid;grid-template-columns:repeat(3,1fr)}
  .spread--inside{top:458px}
  .panel{position:relative;height:100%;overflow:hidden}
  .panel + .panel{border-left:1px solid var(--frame)}

  /* outside — intro panel */
  .intro{padding:12px}
  .intro__card{background:var(--blue);border-radius:10px;height:100%;padding:16px 12px;color:#fff}
  .intro__title{font-size:14px;font-weight:400;line-height:1.1;text-transform:uppercase;letter-spacing:.2px}
  .intro__cols{display:grid;grid-template-columns:1fr 1fr;gap:8px;margin-top:12px}
  .intro__cols h3{font-size:8.5px;font-weight:400;border-bottom:1px solid rgba(255,255,255,.6);padding-bottom:2px;margin:8px 0 4px}
  .intro__cols ul{list-style:none}
  .intro__cols li,.intro__cols p{font-size:5.6px;line-height:1.45}
  .intro__cols li::before{content:"• "}

  /* outside — contact panel */
  .contact{padding:20px 12px 0}
  .hours__head{display:flex;align-items:center;gap:6px;font-size:9px;text-transform:uppercase;margin-bottom:6px}
  .hours{border:2px solid var(--slate);border-collapse:collapse;width:100%}
  .hours td{font-size:7px;padding:3px 5px;border-bottom:1px solid var(--rule)}
  .hours td:first-child{color:var(--muted);width:34px}
  .hours td:last-child{text-align:center}
  .info{background:var(--slate);color:#22313b;padding:8px 10px}
  .info__row{display:flex;gap:8px;align-items:flex-start;margin:4px 0 8px}
  .info__row h4{font-size:8px;font-weight:400;text-transform:uppercase}
  .info__row p{font-size:6.5px;line-height:1.4}
  .contact__web{position:absolute;bottom:18px;left:12px;font-size:8px;color:var(--blue);letter-spacing:.6px}

  /* outside — cover */
  .cover__brand{display:flex;align-items:center;justify-content:center;gap:5px;margin-top:30px}
  .cover__brand span{font-size:13px;color:var(--red);letter-spacing:.5px}
  .cover__mark{width:9px;height:9px;background:var(--red)}
  .cover__tag{text-align:center;font-size:5px;color:var(--muted);letter-spacing:1.5px;margin-top:2px;text-transform:uppercase}
  .cover__photo{position:absolute;top:74px;left:0;right:0;height:230px;background:linear-gradient(160deg,#f3f5f7 0%,#dfe7ec 45%,#c9d6de 100%)}
  .cover__slogan{position:absolute;top:258px;left:18px;color:#fff;font-size:14px;line-height:1.1;letter-spacing:.6px}
  .cover__slogan span{display:block;padding-left:20px}
  .cover__line{position:absolute;top:304px;left:0;right:0;height:3px;background:var(--orange)}
  .cover__greeting{position:absolute;top:326px;left:0;right:0;text-align:center;font-size:8px;line-height:1.8;color:var(--blue);letter-spacing:.4px}
  .cover__greeting span{display:block}

  /* inside */
  .inside__frame{position:absolute;left:120px;top:32px;width:300px;height:240px;border:12px solid var(--frame);border-radius:26px}
  .inside__photos{position:absolute;top:10px;left:12px;display:flex;gap:2px}
  .inside__photos div{width:32px;height:36px}
  .inside__tree{position:absolute;top:12px;left:410px;width:186px;height:186px;background:linear-gradient(180deg,#6f9a4a 0%,#557a36 60%,#6b5a40 100%)}
  .inside__headline{position:absolute;top:60px;left:14px;width:340px;font-size:14.5px;font-weight:400;line-height:1.2;color:var(--orange)}
  .inside__body{position:absolute;top:122px;left:14px;width:290px;font-size:6px;line-height:1.45;color:var(--muted)}
  .services{position:absolute;left:0;right:0;bottom:0;height:220px;background:var(--blue);color:#fff;display:grid;grid-template-columns:203px 1fr 1fr 1fr;padding:8px 8px 0}
  .services__col{padding:0 6px;border-right:1px solid rgba(255,255,255,.5);height:120px}
  .services__col:last-child{border-right:0}
  .services h3{font-size:7px;font-weight:400;text-transform:uppercase;margin-bottom:4px}
  .services h4{font-size:5px;font-weight:400;text-transform:uppercase;margin:3px 0 1px}
  .services ul{list-style:none}
  .services li{font-size:4.6px;line-height:1.4}
  .services .tick li::before{content:"✔ "}
  .services__age{position:relative}
  .services__age-lists{display:grid;grid-template-columns:1fr 1fr;gap:4px;margin-top:8px}
  .services__title{position:absolute;bottom:12px;left:0;right:0;text-align:center;font-size:30px;letter-spacing:2px;color:rgba(255,255,255,.55);padding-left:120px}
</style>
</head>
<body>

<section class="spread spread--outside" aria-label="Brochure outside">
  <div class="panel intro">
    <div class="intro__card">
      <h2 class="intro__title">BRIXACURE provides walk-in healthcare diagnosis and treatment services</h2>
      <div class="intro__cols">
        <div>
          <h3>What we do</h3>
          <ul>
            <li>Urgent care for illness and minor injuries</li>
            <li>Routine checkups and lab tests</li>
            <li>Health education and prevention</li>
          </ul>
          <h3>How it works</h3>
          <p>Convenient location with ample parking. No appointment needed, just walk in.</p>
        </div>
        <div>
          <h3>Why</h3>
          <ul>
            <li>Affordable service</li>
            <li>Short wait times</li>
            <li>Open evenings and weekends</li>
          </ul>
          <h3>Now and future</h3>
          <p>We are dedicated to providing quality care close to home and will keep growing with our community.</p>
        </div>
      </div>
    </div>
  </div>

  <div class="panel contact">
    <div class="hours__head">
      <svg width="12" height="12" viewBox="0 0 12 12" aria-hidden="true"><rect x="1" y="1" width="10" height="10" fill="#333"/><rect x="3" y="3" width="2" height="2" fill="#fff"/><rect x="7" y="3" width="2" height="2" fill="#fff"/><rect x="3" y="7" width="2" height="2" fill="#fff"/><rect x="7" y="7" width="2" height="4" fill="#fff"/></svg>
      Office hours
    </div>
    <table class="hours">
      <tr><td>MON</td><td>9:00am - 9:00pm</td></tr>
      <tr><td>TUE</td><td>9:00am - 9:00pm</td></tr>
      <tr><td>WED</td><td>9:00am - 9:00pm</td></tr>
      <tr><td>THU</td><td>9:00am - 9:00pm</td></tr>
      <tr><td>FRI</td><td>9:00am - 9:00pm</td></tr>
      <tr><td>SAT</td><td>10:00am - 8:00pm</td></tr>
      <tr><td>SUN</td><td>10:00am - 8:00pm</td></tr>
    </table>
    <div class="info">
      <div class="info__row">
        <svg width="14" height="12" viewBox="0 0 14 12" aria-hidden="true"><path d="M1 4 Q7 -1 13 4 L11 5.5 L9.5 4 L4.5 4 L3 5.5 Z" fill="#222"/><rect x="3" y="6" width="8" height="5" rx="1" fill="#222"/><circle cx="7" cy="8.5" r="1.3" fill="#8c9ca8"/></svg>
        <div><h4>Phone</h4><p>(555) 014-2290</p></div>
      </div>
      <div class="info__row">
        <svg width="12" height="14" viewBox="0 0 12 14" aria-hidden="true"><path d="M6 1 A4 4 0 0 1 10 5 C10 8 6 12 6 12 C6 12 2 8 2 5 A4 4 0 0 1 6 1Z" fill="#222"/><circle cx="6" cy="5" r="1.5" fill="#8c9ca8"/></svg>
        <div><h4>Where we are</h4><p>418 Linden Ave.<br>Fairview, MI 48000</p></div>
      </div>
    </div>
    <p class="contact__web">WWW.BRIXA-CURE.COM</p>
  </div>

  <div class="panel cover">
    <div class="cover__brand"><i class="cover__mark"></i><span>BRIXACURE</span></div>
    <p class="cover__tag">Convenience clinic</p>
    <div class="cover__photo" role="img" aria-label="Photo of a smiling doctor in a white coat"></div>
    <p class="cover__slogan">Convenience<span>We Value</span></p>
    <div class="cover__line"></div>
    <p class="cover__greeting">
      <span lang="ko">안녕하세요</span>
      <span lang="zh">您好</span>
      <span lang="ja">こんにちは</span>
      <span lang="en">Hello</span>
    </p>
  </div>
</section>

<section class="spread spread--inside" aria-label="Brochure inside">
  <div class="inside__frame"></div>
  <div class="inside__photos">
    <div role="img" aria-label="Photo of a senior woman outdoors" style="background:linear-gradient(#9cc07a,#d7c6b0)"></div>
    <div role="img" aria-label="Photo of a young woman" style="background:linear-gradient(#d9d3cc,#8a7d74)"></div>
    <div role="img" aria-label="Photo of people jogging" style="background:linear-gradient(#8fb6d8,#7a9a4e)"></div>
    <div role="img" aria-label="Photo of a jumping runner" style="background:linear-gradient(#a6c8e6,#8fae62)"></div>
    <div role="img" aria-label="Photo of a young man" style="background:linear-gradient(#e6e6e6,#6f7f92)"></div>
    <div role="img" aria-label="Photo of a smiling group of friends" style="background:linear-gradient(#d0d8e0,#5d6f86)"></div>
    <div role="img" aria-label="Photo of a student with a laptop" style="background:linear-gradient(#cfd7de,#7b8ea2)"></div>
    <div role="img" aria-label="Photo of a smiling teenage girl" style="background:linear-gradient(#7f9a54,#c8a88a)"></div>
  </div>
  <div class="inside__tree" role="img" aria-label="Photo of a large green tree"></div>
  <h1 class="inside__headline">We are dedicated to providing quality healthcare services at an affordable rate, and easy access that is reliable and convenient.</h1>
  <p class="inside__body">Bis out venis consequos autem ipsande veles et restiunt vitiasimet vendellab ipsus ut venesti untota veri illa nulla quam, sit evelise pre simporuptat. Id ut exceaqui dolorepe ommo qui res am que re plandiatius unt repratur, si od exerum comnihi llecum asperem re molupta tincist.</p>

  <div class="services">
    <div class="services__col services__age">
      <h3>All age group</h3>
      <div class="services__age-lists">
        <div>
          <h4>Respiratory conditions</h4>
          <ul class="tick"><li>Allergies</li><li>Flu</li><li>Sinus Infection</li><li>Sore Throat</li><li>Strep Throat</li><li>Bronchitis</li><li>Colds</li><li>Coughs</li></ul>
          <h4>Head, ear and eye</h4>
          <ul class="tick"><li>Styes</li><li>Pink Eye</li><li>Ear Infection</li></ul>
        </div>
        <div>
          <h4>Skin, hair and nail</h4>
          <ul class="tick"><li>Acne</li><li>Rashes</li><li>Hives</li><li>Minor Burns</li><li>Warts</li><li>Insect Bites</li><li>Lice</li></ul>
          <h4>Digestive and urinary</h4>
          <ul class="tick"><li>Bladder Infection</li><li>Diarrhea</li><li>Nausea</li><li>Urinary Tract Infection</li><li>Vomiting</li></ul>
        </div>
      </div>
    </div>
    <div class="services__col">
      <h3>Adult and senior</h3>
      <ul class="tick">
        <li>Men's and Women's Diagnostic Screenings (Cholesterol Panel, Liver and Kidney Function Tests and Electrolytes, Prostate Specific Antigen, Thyroid Panel, and more)</li>
        <li>Heart Health (C-Reactive Protein, Cholesterol Profile)</li>
        <li>Diabetes Testing (Glucose Screening, Hemoglobin A1c)</li>
        <li>Vaccinations (Flu Shots, Childhood Shots, Adult and Travel Vaccinations)</li>
      </ul>
    </div>
    <div class="services__col">
      <h3>Young adult and children</h3>
      <ul class="tick">
        <li>Nutrition Consultation</li><li>Stress Management</li><li>Fatigue Relief</li><li>Back Pain</li><li>Skin Care</li><li>Camp, Sports, School Physicals</li><li>Travel Medicine</li>
      </ul>
    </div>
    <div class="services__col">
      <h3>Miscellaneous</h3>
      <ul class="tick">
        <li>B12 Shots</li><li>Ear Irrigation</li><li>Flu Instant Test</li><li>Injectable Antibiotics</li><li>Minor Laceration Closure</li><li>Mono Instant Test</li><li>Nebulizer Breathing Treatments</li><li>Pink Eye Instant Test</li><li>Pregnancy Instant Test</li><li>STD Testing</li><li>Steroid Injections</li><li>Strep Instant Test</li><li>Smoking Cessation</li><li>Suture/Staple Removal</li><li>Throat Culture</li><li>Urinalysis Dipstick</li><li>Urine Drug Screen</li>
      </ul>
    </div>
    <p class="services__title">OUR SERVICES</p>
  </div>
</section>

</body>
</html>
```